i would like a business card to leave with customers and potential customers for electrical work and for the supply and install of reverse cycle airconditioning in the domestic and commercial market.
I own my own business and im a sole trader. I have an a'class electrical lisence and also a refrigeration lisence so i am
able to offer complete installations in airconditioning by a fully qualified and lisenced tradesman.
im looking for something that comes across as unique and professional.
i had the coluor black and some gold in mind but open to any coluors.
something like Lanterra Electrical & Refrigeration
or Lanterra Air.
i will use this design on a business card to advertise through summer to help generate installs through the busy season.

Target Market(s)

Mainly domestic house holds through summer who are in need of airconditioning and reliable information to acomadate thier cooling and heating requirements

Industry/Entity Type

Electrical

Requirements
Must have
• Business name- Lanterra
My name- Mark Delford
My mobile no- 0438 517 290
My email- mrdelford@qelvo.com.au
Installation & Decomissioning of aiconditioning split systems
LIC NO: TRK 540316
Nice to have
• Lanterra Electrical & Refrigeration

```html
<!DOCTYPE html>
<html lang="en">
<head>
<meta charset="utf-8">
<title>Lanterra Electrical &amp; Refrigeration – Business Card</title>
<link rel="stylesheet" href="https://fonts.googleapis.com/css2?family=Exo+2:wght@700&family=Open+Sans:wght@400;600&display=swap">
<style>
  :root {
    --sky: #2fa6d8;
    --sky-deep: #1f8fc2;
    --paper: #ffffff;
    --paper-shade: #f1f3f4;
    --ink: #1d1d1d;
    --backdrop: #e4e6e8;
  }
  * { box-sizing: border-box; margin: 0; padding: 0; }
  html, body { width: 1200px; height: 874px; overflow: hidden; }
  body {
    background: var(--backdrop);
    font-family: "Open Sans", Arial, sans-serif;
    display: flex;
    flex-direction: column;
    align-items: center;
    justify-content: center;
    gap: 56px;
  }
  .card {
    width: 620px;
    height: 354px;
    position: relative;
    overflow: hidden;
    box-shadow: 0 6px 18px rgba(0,0,0,.18);
  }

  /* ---------- front ---------- */
  .card--front {
    background: linear-gradient(180deg, var(--paper) 0%, var(--paper-shade) 100%);
  }
  .card--front .end-band {
    position: absolute; top: 0; right: 0;
    width: 22px; height: 100%;
    background: var(--sky);
  }
  .card--front .tagline-band {
    position: absolute; left: 0; bottom: 0;
    width: 100%; height: 46px;
    background: var(--sky);
    display: flex; align-items: center;
    padding-left: 124px;
    color: var(--paper);
    font-size: 15px;
    letter-spacing: .2px;
  }
  .brand {
    position: absolute; left: 34px; top: 206px;
    display: flex; align-items: center; gap: 12px;
  }
  .brand__mark {
    width: 66px; height: 66px;
    border-radius: 50%;
    border: 4px solid var(--sky);
  }
  .brand__name {
    font-family: "Exo 2", Arial, sans-serif;
    font-weight: 700;
    font-size: 40px;
    line-height: 1;
    color: var(--sky);
    letter-spacing: .5px;
    text-transform: uppercase;
  }
  .brand__sub {
    font-size: 13px;
    color: var(--ink);
    margin-top: 3px;
    padding-left: 2px;
  }
  .partner-badge {
    position: absolute; left: 40px; bottom: 6px;
    width: 34px; height: 34px;
    background: var(--paper);
  }
  .contact {
    position: absolute; right: 70px; top: 58px;
    color: var(--ink);
    font-size: 15px;
    line-height: 1.45;
  }
  .contact__name {
    color: var(--sky);
    font-weight: 600;
    font-size: 22px;
    margin-bottom: 4px;
  }

  /* ---------- back ---------- */
  .card--back {
    background: linear-gradient(135deg, var(--sky) 0%, var(--sky-deep) 100%);
    display: flex; flex-direction: column;
    align-items: center; justify-content: center;
    gap: 18px;
    color: var(--paper);
  }
  .card--back .brand__mark {
    width: 120px; height: 120px;
    border: 5px solid var(--paper);
  }
  .card--back .brand__name { color: var(--paper); font-size: 50px; }
  .card--back .brand__sub { color: var(--paper); font-size: 15px; text-align: right; margin-top: 2px; }
</style>
</head>
<body>

  <section class="card card--front" aria-label="Business card front">
    <div class="end-band"></div>

    <div class="contact">
      <p class="contact__name">Mark Delford</p>
      <p>M: 0438 517 290</p>
      <p>E: mrdelford@qelvo.com.au</p>
      <p>LIC NO: TRK 540316</p>
    </div>

    <div class="brand">
      <div class="brand__mark"></div>
      <div>
        <p class="brand__name">Lanterra</p>
        <p class="brand__sub">Electrical &amp; Refrigeration</p>
      </div>
    </div>

    <div class="tagline-band">Installation &amp; Decomissioning of airconditioning split systems</div>

    <div class="partner-badge" role="img" aria-label="Accreditation badge placeholder"></div>
  </section>

  <section class="card card--back" aria-label="Business card back">
    <div class="brand__mark"></div>
    <div>
      <p class="brand__name">Lanterra</p>
      <p class="brand__sub">Electrical &amp; Refrigeration</p>
    </div>
  </section>

</body>
</html>
```